Heron Loan Partners Business Card

We need a business card design for our mortgage servicing company. In addition to servicing the loans of homeowners, we help homeowners with purchasing their homes and any mortgage refinancing. We would like to see designs that use the colors in the logo attached below (gold-ish yellow and navy blue), and any other design you deem fit! The design should communicate a simpler life with smart mortgages provided by Heron.

```html
<!DOCTYPE html>
<html lang="en">
<head>
<meta charset="utf-8">
<title>Heron Loan Partners — Business Card</title>
<link rel="stylesheet" href="https://fonts.googleapis.com/css2?family=Arimo:wght@400;700&display=swap">
<style>
  :root {
    --backdrop: #5b5b5d;
    --paper: #f4f4f2;
    --navy: #1d1a52;
    --navy-deep: #171445;
    --gold: #d7a52a;
    --ink: #3a3a3c;
    --ink-soft: #7a7a80;
    --rule: #c9c9cc;
    --white: #ffffff;
  }
  * { box-sizing: border-box; margin: 0; padding: 0; }
  html, body { width: 1200px; height: 1108px; overflow: hidden; }
  body {
    background: var(--backdrop);
    font-family: "Arimo", Arial, sans-serif;
    display: flex;
    flex-direction: column;
    align-items: center;
    justify-content: center;
    gap: 48px;
  }
  .card {
    width: 840px;
    height: 480px;
    position: relative;
    box-shadow: 0 14px 32px rgba(0,0,0,.35);
  }

  /* Front */
  .card--front { background: var(--paper); display: flex; }
  .brand {
    width: 58%;
    display: flex;
    align-items: center;
    justify-content: center;
    gap: 14px;
  }
  .brand__dot {
    width: 18px; height: 18px; border-radius: 50%;
    background: var(--navy);
  }
  .brand__name {
    font-weight: 700;
    font-size: 64px;
    color: var(--gold);
    letter-spacing: -1px;
  }
  .divider {
    position: absolute;
    left: 58%;
    top: 120px;
    bottom: 120px;
    width: 1px;
    background: var(--rule);
  }
  .contact {
    width: 42%;
    padding: 128px 0 0 34px;
    color: var(--ink);
  }
  .contact__name {
    font-weight: 700;
    font-size: 28px;
    color: var(--navy);
  }
  .contact__title {
    font-size: 15px;
    color: var(--ink-soft);
    margin: 4px 0 22px;
  }
  .contact__address {
    font-size: 16px;
    line-height: 1.35;
    font-style: normal;
    margin-bottom: 16px;
  }
  .contact__list { list-style: none; font-size: 16px; line-height: 1.55; }
  .contact__list li { display: flex; align-items: center; gap: 10px; }
  .contact__list svg { width: 15px; height: 15px; flex: none; }

  /* Back */
  .card--back {
    background: radial-gradient(ellipse at 50% 30%, var(--navy) 0%, var(--navy-deep) 100%);
    display: flex;
    flex-direction: column;
    align-items: center;
    justify-content: center;
  }
  .back-brand {
    display: flex;
    align-items: center;
    gap: 22px;
    margin-top: -20px;
  }
  .back-brand__dot {
    width: 30px; height: 30px; border-radius: 50%;
    background: var(--gold);
  }
  .back-brand__name {
    font-weight: 700;
    font-size: 132px;
    color: var(--gold);
    letter-spacing: -2px;
  }
  .tagline {
    margin-top: 44px;
    font-size: 22px;
    color: var(--white);
  }
</style>
</head>
<body>
  <section class="card card--front" aria-label="Business card front">
    <div class="brand">
      <span class="brand__dot"></span>
      <span class="brand__name">Heron</span>
    </div>
    <span class="divider"></span>
    <div class="contact">
      <h1 class="contact__name">Daniel Reeve</h1>
      <p class="contact__title">President</p>
      <address class="contact__address">412 Alder Court<br>Whitby, Canada 58213</address>
      <ul class="contact__list">
        <li>
          <svg viewBox="0 0 16 16" aria-hidden="true"><path fill="var(--gold)" d="M3.6 1.5l2.2 2.6-1.3 1.7c.9 2 2.5 3.6 4.5 4.5l1.7-1.3 2.6 2.2-1.4 2.3C6.4 15 1 9.6 1.3 2.9z"/></svg>
          555-201-4873
        </li>
        <li>
          <svg viewBox="0 0 16 16" aria-hidden="true"><rect x="4" y="1" width="8" height="14" rx="1.5" fill="none" stroke="var(--gold)" stroke-width="1.6"/><circle cx="8" cy="12.5" r=".9" fill="var(--gold)"/></svg>
          555-309-6621
        </li>
        <li>
          <svg viewBox="0 0 16 16" aria-hidden="true"><rect x="1" y="3.5" width="14" height="9" fill="var(--gold)"/><path d="M1.5 4l6.5 5 6.5-5" fill="none" stroke="var(--paper)" stroke-width="1.2"/></svg>
          info@heronloans.com
        </li>
        <li>
          <svg viewBox="0 0 16 16" aria-hidden="true"><circle cx="8" cy="8" r="7" fill="var(--gold)"/><path d="M1 8h14M8 1c-3 3.5-3 10.5 0 14M8 1c3 3.5 3 10.5 0 14" fill="none" stroke="var(--paper)" stroke-width="1"/></svg>
          www.heronloans.com
        </li>
      </ul>
    </div>
  </section>

  <section class="card card--back" aria-label="Business card back">
    <div class="back-brand">
      <span class="back-brand__dot"></span>
      <span class="back-brand__name">Heron</span>
    </div>
    <p class="tagline">Simpler life with smart mortgages</p>
  </section>
</body>
</html>
```